Plakate für ein Fest
Zielgruppe
Das Kessner Park ist ein Gewerbepark mit unterschiedlichen Mietern von Handwerker über Musiker bis hin zu Vermögensberatung. Wir veranstalten ein Fest für unsere Mieter und möchten dieses Plakat als Einladung nutzen.
Aufgabenstellung
Hintergrund schwarz, Logo verwenden
Get together
BBQ & Cocktails im Kessner Park
am 13.10.2023 ab 18 Uhr
Logo Band wild pebbles
Kinderbereich
Wir freuen uns darauf, alle Mieter mit Familien begrüßen zu dürfen! Auch an die Kleinen haben wir gedacht.

```html
<!DOCTYPE html>
<html lang="de">
<head>
<meta charset="utf-8">
<title>Get Together – BBQ &amp; Cocktails im Kessner Park</title>
<link rel="stylesheet" href="https://fonts.googleapis.com/css2?family=Alfa+Slab+One&family=Staatliches&family=Arimo:wght@700&family=Questrial&family=Playfair+Display:ital,wght@1,700&display=swap">
<style>
  :root {
    --ink: #000000;
    --paper: #ffffff;
    --green: #3fa556;
    --illustration: #3a3a3a;
  }
  * { margin: 0; padding: 0; box-sizing: border-box; }
  html, body { width: 844px; height: 1200px; overflow: hidden; background: var(--ink); }
  .poster {
    position: relative;
    width: 844px; height: 1200px;
    background: var(--ink);
    border: 5px solid var(--green);
    color: var(--paper);
    overflow: hidden;
  }
  .ribbon { position: absolute; left: 218px; top: 90px; width: 380px; height: 110px; }
  .ribbon-title {
    position: absolute; left: 218px; top: 112px; width: 380px;
    text-align: center;
    font-family: "Alfa Slab One", serif;
    font-size: 30px; letter-spacing: 3px;
    color: var(--ink);
    transform: rotate(1.5deg);
  }
  .illustration {
    position: absolute;
    background: radial-gradient(ellipse at center, var(--illustration) 0%, #1c1c1c 70%, var(--ink) 100%);
    border-radius: 12px;
  }
  .illustration-grill { left: 75px; top: 278px; width: 164px; height: 262px; }
  .illustration-tools { left: 260px; top: 190px; width: 325px; height: 268px; }
  .illustration-cocktail { left: 629px; top: 296px; width: 164px; height: 232px; }
  .headline {
    position: absolute; left: 0; width: 100%;
    text-align: center;
    font-family: "Staatliches", sans-serif;
    line-height: 1;
    color: var(--paper);
  }
  .headline-bbq { top: 502px; font-size: 112px; letter-spacing: 14px; }
  .headline-amp { font-family: "Playfair Display", serif; font-style: italic; font-size: 96px; letter-spacing: 0; }
  .headline-cocktails { top: 606px; font-size: 116px; letter-spacing: 16px; padding-left: 16px; }
  .venue {
    position: absolute; top: 746px; left: 0; width: 100%;
    text-align: center;
    font-family: "Alfa Slab One", serif;
    font-size: 35px; letter-spacing: 3px;
  }
  .date-band { position: absolute; left: 75px; top: 824px; width: 718px; height: 92px; }
  .date-text {
    position: absolute; left: 75px; top: 824px; width: 718px; height: 92px;
    display: flex; align-items: center; justify-content: center; gap: 44px;
    font-family: "Arimo", sans-serif; font-weight: 700;
    font-size: 52px; color: var(--paper);
  }
  .invitation {
    position: absolute; top: 952px; left: 0; width: 100%;
    text-align: center;
    font-family: "Questrial", sans-serif;
    font-size: 19.5px; line-height: 1.4;
  }
  .sponsor {
    position: absolute; top: 1064px;
    display: flex; align-items: center; gap: 12px;
    font-family: "Questrial", sans-serif;
    color: var(--paper);
  }
  .sponsor-host { left: 116px; font-size: 30px; line-height: 1; }
  .sponsor-host .mark { width: 46px; height: 46px; background: var(--green); }
  .sponsor-band { left: 415px; top: 1072px; font-size: 42px; letter-spacing: 2px; }
</style>
</head>
<body>
<main class="poster">
  <svg class="ribbon" viewBox="0 0 380 110" aria-hidden="true">
    <polygon points="0,48 40,40 40,100 0,108 18,78" fill="var(--paper)"/>
    <polygon points="380,62 340,56 340,108 380,104 362,82" fill="var(--paper)"/>
    <polygon points="24,8 356,18 352,92 28,80" fill="var(--paper)"/>
  </svg>
  <p class="ribbon-title">GET TOGETHER</p>

  <div class="illustration illustration-grill" role="img" aria-label="Zeichnung eines Kugelgrills mit Rauch"></div>
  <div class="illustration illustration-tools" role="img" aria-label="Zeichnung von gekreuzter Grillgabel und Grillwender vor einer Flamme"></div>
  <div class="illustration illustration-cocktail" role="img" aria-label="Zeichnung eines Cocktailglases mit Zitronenscheibe"></div>

  <h1>
    <span class="headline headline-bbq">BBQ <span class="headline-amp">&amp;</span></span>
    <span class="headline headline-cocktails">COCKTAILS</span>
  </h1>

  <p class="venue">IM KESSNER PARK</p>

  <svg class="date-band" viewBox="0 0 718 92" aria-hidden="true">
    <polygon points="0,0 718,0 694,46 718,92 0,92 24,46" fill="var(--green)"/>
  </svg>
  <p class="date-text"><span>13.10.2023</span><span>18 Uhr</span></p>

  <p class="invitation">Wir freuen uns darauf, alle Mieter mit Familien begrüßen<br>zu dürfen! Auch an die Kleinen haben wir gedacht.</p>

  <div class="sponsor sponsor-host"><span class="mark"></span><span>KESSNER<br>PARK</span></div>
  <div class="sponsor sponsor-band">wild pebbles</div>
</main>
</body>
</html>
```